Business card design needed

I run a Beautician studio (for 7 years now)
I offer
- Velmo Body Sugaring
- Ruby Glaze
- Nails
- Facials
- Manicure
- Foot Treatment
It might not be necessary to list all those treatments?
Maybe the link to the Website is sufficient?
I leave that up to you ...
(more info on www.FernAndDewByLenka.com.au)
Velmo BodySugaring is our biggest success, It replaces waxing.
I would like to incorporate the logo into the Business Card.
We had many complaints regarding our old Business Cards as the Phone Number was to small.
On the backside, we would like a "your next Appointment" section.
Looking forward to you Design, cheers ... Lenka
Industry/Entity Type
Business
Contact Information for Business Card
Fern by Dew by Lenka
14 Korrin Sqr 3942 Dellmere
www.FernAndDewByLenka.com.au
03 9481 2267

```html
<!DOCTYPE html>
<html lang="en">
<head>
<meta charset="utf-8">
<title>Fern &amp; Dew by Lenka – Business Card</title>
<link rel="stylesheet" href="https://fonts.googleapis.com/css2?family=Open+Sans:ital,wght@0,400;0,600;0,700;1,600;1,700&family=Tinos&display=swap">
<style>
  :root {
    --stage: #ece8e3;
    --card: #ffffff;
    --ink: #3a3a3a;
    --ink-soft: #555555;
    --rule: #9a9a9a;
    --brand-orange: #f08a1c;
    --label: #1e1e1e;
  }
  * { box-sizing: border-box; margin: 0; padding: 0; }
  html, body { width: 1200px; height: 788px; overflow: hidden; }
  body {
    background: var(--stage);
    font-family: "Open Sans", Arial, sans-serif;
    color: var(--ink);
    position: relative;
  }
  .side-label { position: absolute; font-size: 21px; color: var(--label); }
  .card {
    position: absolute;
    width: 524px;
    height: 298px;
    background: var(--card);
    border-radius: 20px;
    box-shadow: 0 4px 12px rgba(0,0,0,.25);
    overflow: hidden;
  }
  .card > * { position: absolute; }
  .front { left: 338px; top: 75px; }
  .back-one { left: 54px; top: 446px; }
  .back-two { left: 622px; top: 446px; }

  .studio-name {
    font-size: 29px;
    font-weight: 400;
    letter-spacing: 1px;
    color: var(--ink);
    white-space: nowrap;
  }
  .front .studio-name { left: 33px; top: 40px; }

  .contact-list { left: 32px; top: 213px; list-style: none; font-size: 16px; line-height: 23px; }
  .contact-list li { display: flex; align-items: center; gap: 7px; }
  .contact-list svg { width: 12px; height: 12px; fill: var(--ink); }

  .brand-mark { display: flex; flex-direction: column; align-items: center; }
  .brand-mark .dot { width: 54px; height: 54px; border-radius: 50%; background: var(--brand-orange); }
  .brand-mark .word { margin-top: 6px; font-size: 21px; font-weight: 600; color: var(--ink); }
  .front .brand-mark { left: 392px; top: 184px; }
  .back-two .brand-mark { left: 388px; top: 18px; }
  .back-two .brand-mark .dot { width: 50px; height: 50px; }
  .back-two .brand-mark .word { font-size: 20px; }

  /* Back 1 */
  .back-one .studio-name { left: 0; width: 100%; top: 10px; text-align: center; font-size: 25px; }
  .header-rule { left: 0; top: 50px; width: 100%; height: 1px; background: var(--rule); }
  .section-title { font-style: italic; font-weight: 700; font-size: 17px; color: var(--ink); }
  .offer-title { left: 29px; top: 68px; }
  .offer-list { left: 30px; top: 96px; list-style: none; font-family: "Tinos", "Times New Roman", serif; font-size: 15px; line-height: 20px; color: var(--ink-soft); }
  .offer-list li::before { content: "▪"; font-size: 10px; margin-right: 6px; vertical-align: 2px; }
  .column-rule { left: 207px; top: 68px; width: 2px; height: 146px; background: var(--rule); }
  .appointment-title { left: 243px; top: 68px; }
  .form-line { left: 243px; font-size: 16px; color: var(--ink-soft); display: flex; align-items: flex-end; }
  .form-line .blank { border-bottom: 1px solid var(--ink-soft); height: 18px; margin: 0 4px 0 0; }
  .hours-title { left: 0; width: 478px; top: 237px; text-align: center; font-style: italic; font-weight: 600; font-size: 14px; }
  .hours-line { left: 60px; top: 260px; font-size: 12.5px; white-space: nowrap; }
  .hours-line span + span { margin-left: 46px; }

  /* Back 2 */
  .back-two .hours-heading { left: 32px; top: 28px; font-style: italic; font-weight: 600; font-size: 20px; letter-spacing: 1px; }
  .back-two .hours-detail { left: 30px; top: 60px; font-size: 17px; line-height: 24px; }
  .back-two .divider { left: 28px; top: 116px; width: 466px; height: 1px; background: var(--rule); }
  .back-two .row { font-size: 18px; color: var(--ink); display: flex; align-items: flex-end; white-space: nowrap; }
  .back-two .blank { display: inline-block; border-bottom: 1px solid var(--ink); height: 20px; }
  .days { left: 58px; top: 246px; display: flex; gap: 16px; font-size: 17px; }
  .days span { display: flex; align-items: center; gap: 10px; }
  .days i { width: 23px; height: 23px; border: 1px solid var(--ink); display: inline-block; }
</style>
</head>
<body>
  <div class="side-label" style="left:292px;top:34px">Front</div>
  <div class="side-label" style="left:572px;top:34px">Front</div>
  <div class="side-label" style="left:284px;top:404px">Back - 1</div>
  <div class="side-label" style="left:856px;top:404px">Back - 2</div>

  <section class="card front">
    <h1 class="studio-name">FERN&amp;DEW BY LENKA</h1>
    <ul class="contact-list">
      <li><svg viewBox="0 0 12 12"><path d="M3 1l2 2-1 2c1 1.5 2 2.5 3 3l2-1 2 2-1.5 2C5 11 1 7 1 2.5z"/></svg>03 9481 2267</li>
      <li><svg viewBox="0 0 12 12"><path d="M6 1l5 5H9.5v5h-2.5V8H5v3H2.5V6H1z"/></svg>14 Korrin Sqr, 3942 Dellmere</li>
      <li><svg viewBox="0 0 12 12"><circle cx="6" cy="6" r="5"/></svg>www.FernAndDewByLenka.com.au</li>
    </ul>
    <div class="brand-mark"><span class="dot"></span><span class="word">VELMO</span></div>
  </section>

  <section class="card back-one">
    <h2 class="studio-name">FERN&amp;DEW BY LENKA</h2>
    <div class="header-rule"></div>
    <h3 class="section-title offer-title">I offer</h3>
    <ul class="offer-list">
      <li>Velmo Body Sugaring</li>
      <li>Ruby Glaze</li>
      <li>Nails</li>
      <li>Facials</li>
      <li>Manicure</li>
      <li>Foot Treatment</li>
    </ul>
    <div class="column-rule"></div>
    <h3 class="section-title appointment-title">An Appointment</h3>
    <div class="form-line" style="top:110px">Name<span class="blank" style="width:216px"></span></div>
    <div class="form-line" style="top:150px">Date<span class="blank" style="width:226px"></span></div>
    <div class="form-line" style="top:190px">time<span class="blank" style="width:158px"></span>am / pm</div>
    <div class="hours-title">Hours of Operation</div>
    <div class="hours-line"><span>Mon. to Fri.&nbsp; 7.30am - 7.00pm</span><span>Sat. 7.30am - 12.00pm</span></div>
  </section>

  <section class="card back-two">
    <h3 class="hours-heading">Hours of Operation</h3>
    <p class="hours-detail">Monday to Friday -&nbsp; 7.30am - 7.00pm<br>Saturday - 7.30am - 12.00pm</p>
    <div class="brand-mark"><span class="dot"></span><span class="word">VELMO</span></div>
    <div class="divider"></div>
    <div class="row" style="left:45px;top:142px"><span class="blank" style="width:260px"></span>&nbsp;has an appointment</div>
    <div class="row" style="left:34px;top:192px">Date :&nbsp;<span class="blank" style="width:38px"></span>&nbsp; / &nbsp;<span class="blank" style="width:40px"></span>&nbsp; / &nbsp;<span class="blank" style="width:48px"></span>&nbsp; @ &nbsp;<span class="blank" style="width:38px"></span>&nbsp; : &nbsp;<span class="blank" style="width:50px"></span>am / pm</div>
    <div class="days">
      <span><i></i>Mon.</span>
      <span><i></i>Tue.</span>
      <span><i></i>Wed.</span>
      <span><i></i>Thu.</span>
      <span><i></i>Fri.</span>
    </div>
  </section>
</body>
</html>
```